Calder Vane LED - E- Commerce site

We need a website designed for an LED Billboard company that sells:
1) LED Billboards (Sales & Rental)
2) LED Gas Station lights
3) Truss Systems (Sales & Rental)
4) Sound Systems (Sales & Rental)

Attached are websites that sell similar products as Calder Vane LED. Target market is for business, property managers and event coordinators.
This site will need to be an e-commerce site where customers can purchase the product directly from the site. What I'm looking for is a design layout to start.

Conceptual Web Designs:
http://192.0.2.47:8087/index.html
http://www.pmvdisplay.example/
http://www.auralomaaudio.example/
http://www.quillmarkpanel.example/

Attached is the logo of the company: Please note that the new spelling of the logo is "Calder Vane LED" using domain " CalderVaneLED.com

Industry/Entity Type

Gas Station

Number of Pages Required

5+ page

Requirements
Must have
• 1) E-Commerce - Customers will need to be able to order product from the site.
• 2) Customers will also have the option to rent the product as well.
Nice to have
• I like the image of the attached website, that has a video clip loop
• http://www.quillmarkpanel.example/

```html
<!DOCTYPE html>
<html lang="en">
<head>
<meta charset="utf-8">
<title>Calder Vane LED</title>
<link rel="stylesheet" href="https://fonts.googleapis.com/css2?family=Open+Sans:wght@400;600;700&display=swap">
<style>
:root{
  --ink:#141414;
  --header:#151515;
  --nav:#e6e6e6;
  --gold:#f5b800;
  --orange:#f07b1d;
  --pink:#d23c7c;
  --green:#4aae4a;
  --red:#d8262c;
  --leaf:#3aa83a;
  --blue:#1b4f8f;
  --navy:#1f3f7a;
  --magenta:#d0186c;
  --text:#555;
  --muted:#888;
  --line:#d6d6d6;
  --band:#f4f4f4;
  --foot:#e9e9e9;
  --bar:#1a1a1a;
}
*{box-sizing:border-box;margin:0;padding:0}
html,body{width:1200px;height:2284px;overflow:hidden}
body{position:relative;background:#fff;font-family:"Open Sans",Arial,sans-serif;color:var(--text)}
.abs{position:absolute}

/* header */
.site-header{position:absolute;left:0;top:0;width:1200px;height:128px;background:var(--header)}
.brand{position:absolute;left:132px;top:30px;display:flex;align-items:center;gap:12px}
.brand-mark{width:54px;height:54px;border-radius:50%;background:var(--gold)}
.brand-name{font-size:22px;font-weight:700;color:var(--gold);line-height:1.1;width:120px}
.search{position:absolute;left:611px;top:24px;width:205px;height:36px;border:1px solid #555;border-radius:3px;background:#1d1d1d}
.search span{position:absolute;left:14px;top:9px;font-size:11px;color:#888}
.search svg{position:absolute;right:10px;top:9px}
.contact-item{position:absolute;top:26px;text-align:right;color:#fff}
.contact-item small{display:block;font-size:10px;color:#ddd}
.contact-item b{font-size:12px;font-weight:600}
.round-btn{position:absolute;top:24px;width:36px;height:36px;border-radius:50%;display:flex;align-items:center;justify-content:center}
.main-nav{position:absolute;top:88px;left:430px;width:636px;display:flex;justify-content:space-between;font-size:12.5px}
.main-nav a{color:var(--nav);text-decoration:none}
.main-nav a.active{color:var(--gold)}

/* hero */
.hero{position:absolute;left:0;top:128px;width:1200px;height:405px;background:radial-gradient(ellipse at 55% 45%,#f3c23a 0%,#d79a00 55%,#8a5d00 100%)}
.play{position:absolute;left:559px;top:162px}
.dots{position:absolute;left:562px;top:496px;width:75px;height:18px;border-radius:9px;background:rgba(60,40,0,.55);display:flex;align-items:center;justify-content:center;gap:8px}
.dots i{width:7px;height:7px;border-radius:50%;background:#fff}
.dots i.on{background:none;border:1.5px solid #fff}

/* product rows */
.row{position:absolute;left:132px;width:934px}
.row h2{font-size:24px;font-weight:400;line-height:1}
.arrows{position:absolute;right:0;top:2px;display:flex;gap:2px}
.cards{position:absolute;left:0;top:29px;display:flex;gap:17px}
.card{width:221px;height:206px;border:1px solid var(--line);padding:5px;background:#fff;position:relative}
.card .media{height:146px}
.card p{text-align:center;font-size:12px;color:#444;margin-top:21px}
.overlay{position:absolute;left:5px;top:5px;width:209px;height:146px;background:rgba(20,20,20,.86);color:#fff;text-align:center;padding:30px 22px 0}
.overlay h3{font-size:12.5px;font-weight:600;margin-bottom:10px}
.overlay p{font-size:10px;color:#bbb;line-height:1.45;margin:0}
.overlay .price{font-size:12px;color:#fff;margin-top:12px}
.card-actions{display:flex;justify-content:center;gap:16px;margin-top:14px}

/* about */
.about{position:absolute;left:0;top:1855px;width:1200px;height:181px;background:var(--band)}
.about h2{position:absolute;left:134px;top:30px;font-size:23px;font-weight:400;color:var(--magenta)}
.about p{position:absolute;left:134px;top:72px;width:932px;font-size:10.5px;line-height:20px;color:var(--muted)}

/* footer */
.site-footer{position:absolute;left:0;top:2036px;width:1200px;height:184px;background:var(--foot)}
.foot-col{position:absolute;top:28px}
.foot-col h4{font-size:12px;font-weight:400;color:#222;margin-bottom:10px}
.foot-col li{list-style:none;font-size:10.5px;color:#666;line-height:21px;padding-left:10px;position:relative}
.foot-col li::before{content:"";position:absolute;left:0;top:9px;width:3px;height:3px;border-radius:50%;background:#777}
.divider{position:absolute;top:26px;width:1px;height:124px;background:#cfcfcf}
.bottom-bar{position:absolute;left:0;top:2220px;width:1200px;height:64px;background:var(--bar)}
.bottom-bar small{position:absolute;left:133px;top:24px;font-size:10.5px;color:#ccc}
.pay{position:absolute;top:24px;width:25px;height:16px;border-radius:2px}
.social{position:absolute;top:18px;width:27px;height:27px;border-radius:50%}
</style>
</head>
<body>

<header class="site-header">
  <div class="brand"><span class="brand-mark"></span><span class="brand-name">Calder Vane LED</span></div>
  <div class="search"><span>Search</span>
    <svg width="16" height="16" viewBox="0 0 16 16"><circle cx="6.5" cy="6.5" r="4.5" fill="none" stroke="#f07b1d" stroke-width="2"/><line x1="10" y1="10" x2="14" y2="14" stroke="#f07b1d" stroke-width="2.4" stroke-linecap="round"/></svg>
  </div>
  <div class="contact-item" style="right:282px"><small>Call us on</small><b>555 014 2297</b></div>
  <div class="round-btn" style="left:926px;background:var(--pink)">
    <svg width="16" height="16" viewBox="0 0 16 16"><path d="M4 2l2.5 3-1.5 1.5c.8 1.8 2.2 3.2 4 4L10.5 9l3 2.5-1.5 2C7 13.5 2.5 9 2.5 3.5z" fill="#fff"/></svg>
  </div>
  <div class="contact-item" style="right:177px"><small>My Cart</small><b>$00.00</b></div>
  <div class="round-btn" style="left:1030px;background:var(--green)">
    <svg width="16" height="16" viewBox="0 0 16 16"><path d="M1 2h2.5l2 8h7.5l1.5-6H5" fill="none" stroke="#fff" stroke-width="1.8"/><circle cx="6.5" cy="13" r="1.3" fill="#fff"/><circle cx="12" cy="13" r="1.3" fill="#fff"/></svg>
  </div>
  <nav class="main-nav">
    <a class="active" href="#">Home</a><a href="#">LED Billboards</a><a href="#">Gas Station lights</a><a href="#">Trusses</a><a href="#">Sound Systems</a><a href="#">About us</a><a href="#">Contact us</a>
  </nav>
</header>

<section class="hero" role="img" aria-label="Gas station forecourt at night under a canopy of LED lights, tinted gold, with a video play button">
  <svg class="play" width="82" height="82" viewBox="0 0 82 82"><circle cx="41" cy="41" r="37" fill="none" stroke="#fff" stroke-width="5"/><path d="M32 24l26 17-26 17z" fill="#fff"/></svg>
  <div class="dots"><i class="on"></i><i></i><i></i><i></i></div>
</section>

<!-- LED Billboards -->
<section class="row" style="top:590px">
  <h2 style="color:var(--red)">LED Billboards</h2>
  <div class="arrows">
    <svg width="18" height="18" viewBox="0 0 18 18"><circle cx="9" cy="9" r="8" fill="none" stroke="var(--orange)" stroke-width="1.5"/><path d="M11 5l-4 4 4 4" fill="none" stroke="var(--orange)" stroke-width="1.8"/></svg>
    <svg width="18" height="18" viewBox="0 0 18 18"><circle cx="9" cy="9" r="8" fill="none" stroke="#aaa" stroke-width="1.5"/><path d="M7 5l4 4-4 4" fill="none" stroke="#aaa" stroke-width="1.8"/></svg>
  </div>
  <div class="cards">
    <div class="card">
      <div class="media" role="img" aria-label="LED billboard screen at night" style="background:linear-gradient(135deg,#3a2a4a,#121212)"></div>
      <div class="overlay">
        <h3>Fusce magna magna gravida</h3>
        <p>Aliquam ornare, ligula quis molestie accumsan, dolor magna vestibulum mi, ut luctus risus nibh</p>
        <div class="price">$00.00</div>
      </div>
      <div class="card-actions">
        <svg width="18" height="16" viewBox="0 0 18 16"><path d="M1 2h3l2 8h8l2-6H5" fill="none" stroke="var(--red)" stroke-width="2"/><circle cx="7" cy="13.5" r="1.5" fill="var(--red)"/><circle cx="13" cy="13.5" r="1.5" fill="var(--red)"/></svg>
        <svg width="20" height="14" viewBox="0 0 20 14"><path d="M1 7c3-5 15-5 18 0-3 5-15 5-18 0z" fill="none" stroke="#999" stroke-width="1.6"/><circle cx="10" cy="7" r="2.6" fill="#999"/></svg>
      </div>
    </div>
    <div class="card"><div class="media" role="img" aria-label="City street lined with LED billboards at night" style="background:linear-gradient(160deg,#c2303a,#2d3a6a 55%,#141824)"></div><p>Fusce magna magna gravida</p></div>
    <div class="card"><div class="media" role="img" aria-label="Downtown square with large LED screens at dusk" style="background:linear-gradient(170deg,#4d86c8,#7a5a6a 55%,#3a2a2a)"></div><p>Fusce magna magna gravida</p></div>
    <div class="card"><div class="media" role="img" aria-label="Building facade covered with lit LED billboards" style="background:linear-gradient(180deg,#2a2f4a,#6a5a7a 50%,#141414)"></div><p>Fusce magna magna gravida</p></div>
  </div>
</section>

<!-- Gas Station lights -->
<section class="row" style="top:908px">
  <h2 style="color:var(--leaf)">Gas Station lights</h2>
  <div class="arrows">
    <svg width="18" height="18" viewBox="0 0 18 18"><circle cx="9" cy="9" r="8" fill="none" stroke="var(--leaf)" stroke-width="1.5"/><path d="M11 5l-4 4 4 4" fill="none" stroke="var(--leaf)" stroke-width="1.8"/></svg>
    <svg width="18" height="18" viewBox="0 0 18 18"><circle cx="9" cy="9" r="8" fill="none" stroke="#aaa" stroke-width="1.5"/><path d="M7 5l4 4-4 4" fill="none" stroke="#aaa" stroke-width="1.8"/></svg>
  </div>
  <div class="cards">
    <div class="card"><div class="media" role="img" aria-label="Gas station canopy lit at dusk" style="background:linear-gradient(180deg,#1d3a6a,#b05a2a 55%,#1a1a22)"></div><p>Fusce magna magna gravida</p></div>
    <div class="card"><div class="media" role="img" aria-label="Fuel pumps under bright canopy lights" style="background:linear-gradient(180deg,#d8d0b0,#c2a820 50%,#2a3a5a)"></div><p>Fusce magna magna gravida</p></div>
    <div class="card"><div class="media" role="img" aria-label="Station forecourt under white LED canopy" style="background:linear-gradient(180deg,#1e3a7a,#d8d8e0 55%,#6a6a6a)"></div><p>Fusce magna magna gravida</p></div>
    <div class="card"><div class="media" role="img" aria-label="Gas station with blue canopy lights at night" style="background:linear-gradient(180deg,#0a0f2a,#2a4aa0 55%,#101018)"></div><p>Fusce magna magna gravida</p></div>
  </div>
</section>

<!-- Trusses -->
<section class="row" style="top:1226px">
  <h2 style="color:var(--blue)">Trusses</h2>
  <div class="arrows">
    <svg width="18" height="18" viewBox="0 0 18 18"><circle cx="9" cy="9" r="8" fill="none" stroke="var(--blue)" stroke-width="1.5"/><path d="M11 5l-4 4 4 4" fill="none" stroke="var(--blue)" stroke-width="1.8"/></svg>
    <svg width="18" height="18" viewBox="0 0 18 18"><circle cx="9" cy="9" r="8" fill="none" stroke="#aaa" stroke-width="1.5"/><path d="M7 5l4 4-4 4" fill="none" stroke="#aaa" stroke-width="1.8"/></svg>
  </div>
  <div class="cards">
    <div class="card"><div class="media" role="img" aria-label="Truss frame holding a blank screen" style="background:radial-gradient(ellipse at 50% 45%,#e0e0e0,#5a5a5a 60%,#1a1a1a)"></div><p>Fusce magna magna gravida</p></div>
    <div class="card"><div class="media" role="img" aria-label="Stage truss with lit panel on a wooden floor" style="background:radial-gradient(ellipse at 50% 40%,#cfcfcf,#3a3a3a 60%,#111)"></div><p>Fusce magna magna gravida</p></div>
    <div class="card"><div class="media" role="img" aria-label="Two truss-mounted panels in a dark room" style="background:radial-gradient(ellipse at 50% 45%,#8a8a8a,#222 65%,#0c0c0c)"></div><p>Fusce magna magna gravida</p></div>
    <div class="card"><div class="media" role="img" aria-label="Empty hall with roof truss structure" style="background:linear-gradient(180deg,#6a7a8a,#c8d0d8 50%,#8a9098)"></div><p>Fusce magna magna gravida</p></div>
  </div>
</section>

<!-- Sound Systems -->
<section class="row" style="top:1544px">
  <h2 style="color:var(--navy)">Sound Systems</h2>
  <div class="arrows">
    <svg width="18" height="18" viewBox="0 0 18 18"><circle cx="9" cy="9" r="8" fill="none" stroke="var(--navy)" stroke-width="1.5"/><path d="M11 5l-4 4 4 4" fill="none" stroke="var(--navy)" stroke-width="1.8"/></svg>
    <svg width="18" height="18" viewBox="0 0 18 18"><circle cx="9" cy="9" r="8" fill="none" stroke="#aaa" stroke-width="1.5"/><path d="M7 5l4 4-4 4" fill="none" stroke="#aaa" stroke-width="1.8"/></svg>
  </div>
  <div class="cards">
    <div class="card"><div class="media" role="img" aria-label="Close-up of a loudspeaker" style="background:radial-gradient(circle at 40% 50%,#bdbdbd,#3a3a3a 55%,#0e0e0e)"></div><p>Fusce magna magna gravida</p></div>
    <div class="card"><div class="media" role="img" aria-label="Pair of black speakers" style="background:radial-gradient(circle at 70% 55%,#6a6a6a,#1c1c1c 60%,#080808)"></div><p>Fusce magna magna gravida</p></div>
    <div class="card"><div class="media" role="img" aria-label="Home audio setup in a living room" style="background:linear-gradient(180deg,#e8e8e8,#6a5040 60%,#2a1e18)"></div><p>Fusce magna magna gravida</p></div>
    <div class="card"><div class="media" role="img" aria-label="Stacked road cases of sound equipment" style="background:linear-gradient(180deg,#4a4a4a,#2a2a2a 60%,#5a5a5a)"></div><p>Fusce magna magna gravida</p></div>
  </div>
</section>

<section class="about">
  <h2>About Calder Vane LED</h2>
  <p>Nulla facilisi. Vestibulum vehicula, risus ac convallis efficitur, quam purus feugiat lectus, vel consequat purus nisi blandit diam. Aliquam id iaculis erat. Mauris convallis magna ut purus porttitor pellentesque. Nullam faucibus fringilla accumsan. Morbi vitae est eu risus consequat volutpat. Pellentesque eleifend, sapien vel rutrum tempus, ligula libero pellentesque quam, id finibus enim eros in nisl. Fusce magna magna, gravida nec sem sed, mollis convallis dolor. In dapibus nulla in mauris aliquet congue. Morbi dictum lobortis justo non suscipit. Nam suscipit dolor eget ipsum molestie, eget gravida dolor efficitur. Etiam ultricies velit vitae aliquam ullamcorper. Vivamus efficitur tristique magna a dapibus. Duis quis mi tortor. Praesent quis diam elit.</p>
</section>

<footer class="site-footer">
  <div class="foot-col" style="left:132px"><h4>LED Billboards</h4><ul><li>Integer vitae ligula</li><li>Aenean ullamcorper</li><li>Fusce euismod</li><li>Sed ligula metus</li><li>Nam suscipit</li></ul></div>
  <div class="divider" style="left:283px"></div>
  <div class="foot-col" style="left:332px"><h4>Trusses</h4><ul><li>Integer vitae ligula</li><li>Aenean ullamcorper</li><li>Fusce euismod</li><li>Sed ligula metus</li><li>Nam suscipit</li></ul></div>
  <div class="divider" style="left:496px"></div>
  <div class="foot-col" style="left:556px"><h4>Gas Station lights</h4><ul><li>Integer vitae ligula</li><li>Aenean ullamcorper</li><li>Fusce euismod</li><li>Sed ligula metus</li><li>Nam suscipit</li></ul></div>
  <div class="divider" style="left:728px"></div>
  <div class="foot-col" style="left:787px"><h4>Service &amp; Support</h4><ul><li>Customer Care</li><li>FAQ</li><li>Fusce euismod</li><li>Sed ligula metus</li><li>Nam suscipit</li></ul></div>
  <div class="divider" style="left:946px"></div>
  <div class="foot-col" style="left:1002px"><h4>My Account</h4><ul><li>My Cart</li><li>Checkout</li><li>My Wishlist</li><li>Register</li><li>Log in</li></ul></div>
</footer>

<div class="bottom-bar">
  <small>Copyright &copy; 2016 Calder Vane LED. All rights reserved.</small>
  <span class="pay" style="left:850px;background:#e8a020"></span>
  <span class="pay" style="left:880px;background:#3a7ac8"></span>
  <span class="pay" style="left:910px;background:#e8a020"></span>
  <span class="pay" style="left:938px;background:#3a7ac8"></span>
  <span class="social" style="left:974px;background:#3b5998"></span>
  <span class="social" style="left:1006px;background:#2aa3e0"></span>
  <span class="social" style="left:1038px;background:#1a74b0"></span>
</div>

</body>
</html>
```